Design a New Business Card for Our Company

We are looking for fresh, unique, and a modern business card that reflects our roots as digital marketing agency focused on SEM.

Industry/Entity Type

Marketing

Contact Information for Business Card

looking for very unique out of the box designs. clean and modern that compliments our logo

Requirements
Must have
• colors should match our logo
• Front should have name, address, email, and phone/fax of the person, phone/fax are the same number
• back should have our url

```html
<!DOCTYPE html>
<html lang="en">
<head>
<meta charset="utf-8">
<title>Brightpath Solutions — Business Card</title>
<link rel="stylesheet" href="https://fonts.googleapis.com/css2?family=Open+Sans:wght@400;600;700&display=swap">
<style>
  :root {
    --brand-blue: #5a93cf;
    --accent-grey: #b4b4b4;
    --ink: #333333;
    --muted: #9a9a9a;
    --paper: #ffffff;
    --backdrop: #2b2b2b;
  }
  * { margin: 0; padding: 0; box-sizing: border-box; }
  html, body { width: 1200px; height: 907px; overflow: hidden; }
  body {
    background: var(--backdrop);
    font-family: "Open Sans", Arial, sans-serif;
    position: relative;
  }
  .card {
    position: absolute;
    width: 525px;
    height: 300px;
    top: 303px;
    overflow: hidden;
    box-shadow: 0 10px 30px rgba(0,0,0,.45);
  }
  .card--front { left: 50px; background: var(--paper); }
  .card--back { left: 625px; background: var(--brand-blue); }

  .front-shapes { position: absolute; inset: 0; }
  .brand {
    position: absolute;
    display: flex;
    align-items: center;
    gap: 10px;
    font-weight: 700;
    letter-spacing: -0.5px;
  }
  .brand__dot { border-radius: 50%; flex: none; }
  .card--front .brand { top: 30px; right: 34px; font-size: 24px; color: var(--accent-grey); }
  .card--front .brand__dot { width: 20px; height: 20px; background: var(--brand-blue); }

  .person { position: absolute; left: 34px; top: 102px; }
  .person__name { color: var(--brand-blue); font-weight: 700; font-size: 17px; }
  .person__role { color: var(--muted); font-size: 12px; margin-top: 1px; }

  .contact {
    position: absolute; left: 34px; top: 160px;
    color: var(--ink); font-size: 13px; line-height: 18px; list-style: none;
  }
  .contact__row { display: flex; align-items: center; gap: 7px; }
  .contact__icon { width: 13px; height: 13px; fill: var(--brand-blue); flex: none; }

  .front-url {
    position: absolute; left: 34px; bottom: 10px;
    color: var(--paper); font-size: 14px; letter-spacing: .3px;
  }

  .card--back .brand {
    left: 50%; top: 118px; transform: translateX(-50%);
    font-size: 40px; color: var(--paper); white-space: nowrap;
  }
  .card--back .brand__dot { width: 30px; height: 30px; background: var(--paper); }
  .back-url {
    position: absolute; right: 42px; bottom: 34px;
    color: var(--paper); font-size: 14px; letter-spacing: .3px;
  }
</style>
</head>
<body>

  <section class="card card--front" aria-label="Business card front">
    <svg class="front-shapes" width="525" height="300" viewBox="0 0 525 300" aria-hidden="true">
      <polygon points="330,206 525,206 525,214 338,214" fill="var(--accent-grey)"/>
      <polygon points="0,262 300,262 312,246 322,232 525,232 525,300 0,300" fill="var(--brand-blue)"/>
      <polygon points="300,262 322,262 330,240 322,232 312,246" fill="var(--brand-blue)"/>
    </svg>

    <div class="brand"><span class="brand__dot"></span>brightpath solutions</div>

    <div class="person">
      <p class="person__name">Dana Whitfield</p>
      <p class="person__role">Owner</p>
    </div>

    <ul class="contact">
      <li class="contact__row">N. 8 Harbor Lane, Suite 200,</li>
      <li class="contact__row">Tacoma, WA 98401</li>
      <li class="contact__row">
        <svg class="contact__icon" viewBox="0 0 16 16" aria-hidden="true"><path d="M3 1h3l1.5 4-2 1.3a9 9 0 0 0 4.2 4.2L11 8.5l4 1.5v3a2 2 0 0 1-2 2A12 12 0 0 1 1 3a2 2 0 0 1 2-2z"/></svg>
        555.210.4477
      </li>
      <li class="contact__row">
        <svg class="contact__icon" viewBox="0 0 16 16" aria-hidden="true"><rect x="3" y="1" width="10" height="5"/><rect x="1" y="6" width="14" height="7" rx="1"/><rect x="4" y="10" width="8" height="5" fill="#fff"/></svg>
        555.210.4477
      </li>
      <li class="contact__row">
        <svg class="contact__icon" viewBox="0 0 16 16" aria-hidden="true"><path d="M1 3h14v10H1z"/><path d="M1 3l7 6 7-6" fill="none" stroke="#fff" stroke-width="1.4"/></svg>
        hello@brightpathsolutions.com
      </li>
    </ul>

    <p class="front-url">www.brightpathsolutions.com</p>
  </section>

  <section class="card card--back" aria-label="Business card back">
    <div class="brand"><span class="brand__dot"></span>brightpath solutions</div>
    <p class="back-url">www.brightpathsolutions.com</p>
  </section>

</body>
</html>
```